Business Card Design

I already have a company logo for my company. I have a logo for the manufacturer we represent. I want a professional business card design.

```html
<!DOCTYPE html>
<html lang="en">
<head>
<meta charset="utf-8">
<title>Signalpoint Group – Business Card</title>
<link rel="stylesheet" href="https://fonts.googleapis.com/css2?family=Open+Sans:wght@400;600;700;800&display=swap">
<style>
  :root{
    --page:#222223;
    --card-dark:#1f1e22;
    --gold:#b98e2c;
    --red:#e31b25;
    --white:#ffffff;
    --silver:#d9d9dc;
    --green-deep:#10301a;
    --green-mid:#1b4a26;
    --green-light:#236b33;
  }
  *{box-sizing:border-box;margin:0;padding:0}
  html,body{width:1200px;height:780px;overflow:hidden;background:var(--page)}
  body{font-family:"Open Sans",Arial,sans-serif;position:relative}

  .card{position:absolute;width:520px;height:300px;top:240px;overflow:hidden;
        box-shadow:0 18px 40px rgba(0,0,0,.55)}
  .card--front{left:50px;background:var(--card-dark)}
  .card--back{left:630px}

  .brand{position:absolute;display:flex;align-items:center;gap:10px;white-space:nowrap;
         font-weight:800;color:var(--white);letter-spacing:.04em;text-transform:uppercase}
  .brand__dot{width:16px;height:16px;border-radius:50%;background:var(--red);flex:none}
  .card--front .brand--main{top:62px;right:70px;font-size:22px}

  .band{position:absolute;top:160px;left:0;width:100%;height:96px}
  .band__gold{position:absolute;left:0;top:0;width:52%;height:100%;background:var(--gold);
              clip-path:polygon(0 0,100% 0,82% 100%,0 100%)}
  .band__red{position:absolute;right:0;top:0;width:58%;height:100%;background:var(--red);
             clip-path:polygon(18% 0,100% 0,100% 100%,0 100%)}

  .person{position:absolute;left:26px;top:18px}
  .person__name{font-size:22px;font-weight:700;color:var(--white);line-height:1.1;white-space:nowrap}
  .person__name .first{color:var(--red)}
  .person__role{font-size:13px;color:var(--white);margin-top:4px}

  .brand--band{top:40px;left:232px;font-size:10px;gap:6px}
  .brand--band .brand__dot{width:9px;height:9px;background:var(--white)}

  .contacts{position:absolute;left:330px;top:12px;list-style:none;color:var(--white);
            font-size:13px;line-height:24px;white-space:nowrap}
  .contacts li{display:flex;align-items:center;gap:8px}
  .contacts svg{width:12px;height:12px;flex:none}

  .address{position:absolute;left:26px;top:270px;font-size:12px;color:var(--silver);white-space:nowrap}

  .back__texture{position:absolute;inset:0;
     background:radial-gradient(ellipse at 45% 40%,var(--green-deep) 0%,var(--green-mid) 55%,var(--green-light) 100%)}
  .card--back .brand--main{top:50%;left:50%;transform:translate(-50%,-50%);font-size:26px}
</style>
</head>
<body>

<section class="card card--front" aria-label="Business card front">
  <div class="brand brand--main"><span class="brand__dot"></span>Signalpoint Group LLC</div>

  <div class="band">
    <div class="band__gold"></div>
    <div class="band__red"></div>

    <div class="person">
      <p class="person__name"><span class="first">Maren</span> Kovacic</p>
      <p class="person__role">Managing Director</p>
    </div>

    <div class="brand brand--band"><span class="brand__dot"></span>Signalpoint</div>

    <ul class="contacts">
      <li>
        <svg viewBox="0 0 16 16" aria-hidden="true"><path fill="#fff" d="M3.6 1.5l2.2 2.6-1.3 1.6c.9 2.2 2.6 3.9 4.8 4.8l1.6-1.3 2.6 2.2-1.3 2.3C7.4 13.4 2.6 8.6 1.3 2.8z"/></svg>
        (555) 214-0387
      </li>
      <li>
        <svg viewBox="0 0 16 16" aria-hidden="true"><rect x="1" y="3.5" width="14" height="9" rx="1" fill="#fff"/><path d="M1.5 4l6.5 5 6.5-5" stroke="#e31b25" stroke-width="1.3" fill="none"/></svg>
        hello@signalpoint.example
      </li>
      <li>
        <svg viewBox="0 0 16 16" aria-hidden="true"><circle cx="8" cy="8" r="6.5" fill="none" stroke="#fff" stroke-width="1.5"/><path d="M1.5 8h13M8 1.5c-3 3.5-3 9.5 0 13M8 1.5c3 3.5 3 9.5 0 13" stroke="#fff" stroke-width="1.2" fill="none"/></svg>
        www.signalpoint.example
      </li>
    </ul>
  </div>

  <p class="address">2480 Harbor View Dr #12, Palm Bay, FL 32905, USA</p>
</section>

<section class="card card--back" aria-label="Business card back">
  <div class="back__texture" role="img" aria-label="Green background with radiating stripe texture"></div>
  <div class="brand brand--main"><span class="brand__dot"></span>Signalpoint Group LLC</div>
</section>

</body>
</html>
```